Business Card Design for company

We want new business cards. We'd like something different-- yet still highly professional. Our tagline is Providing leadership, delivering success. Stock photos are ok, as long as they are relevant and look upscale.

Target Market(s)

Architecture/Business Management Consulting/Engineering Consulting

Contact Information for Business Card

dark gray background with pops of blue might be good, but you tell me. You're the designers. Rounded corners might be nice, but again, you tell me.

Font styles to use
Serif
Sans Serif

Colors
3276b5
5c5c5c
9d9d9d
fbfbfb

Requirements
Nice to have
• Something different, but still very professional.

```html
<!DOCTYPE html>
<html lang="en">
<head>
<meta charset="UTF-8">
<title>Norvale Group — Business Card</title>
<link href="https://fonts.googleapis.com/css2?family=Work+Sans:wght@400;500;600&display=swap" rel="stylesheet">
<style>
  :root {
    --brand-blue: #3276b5;
    --brand-blue-deep: #1f5a8f;
    --ink-gray: #5c5c5c;
    --soft-gray: #9d9d9d;
    --paper: #fbfbfb;
    --stage: #3a3a3a;
  }
  * { margin: 0; padding: 0; box-sizing: border-box; }
  html, body { width: 1200px; height: 900px; overflow: hidden; }
  body {
    background: var(--stage);
    font-family: "Work Sans", Arial, sans-serif;
    display: flex;
    flex-direction: column;
    align-items: center;
    justify-content: center;
    gap: 44px;
  }
  .card {
    position: relative;
    width: 700px;
    height: 400px;
    overflow: hidden;
    box-shadow: 0 14px 30px rgba(0,0,0,0.45);
  }

  /* Front */
  .card-front { background: linear-gradient(160deg, #ffffff 0%, var(--paper) 60%, #efefef 100%); }
  .holder { position: absolute; left: 44px; top: 56px; }
  .holder-name {
    color: var(--brand-blue);
    font-size: 30px; font-weight: 500; letter-spacing: 2px; text-transform: uppercase;
  }
  .holder-role { color: var(--ink-gray); font-size: 15px; margin-top: 4px; }
  .divider {
    position: absolute; left: 44px; right: 44px; top: 178px;
    height: 2px; background: var(--brand-blue); opacity: 0.8;
  }
  .contact { position: absolute; left: 44px; top: 200px; list-style: none; }
  .contact li {
    display: flex; align-items: center; gap: 10px;
    color: var(--ink-gray); font-size: 16px; line-height: 30px;
  }
  .contact svg { width: 14px; height: 14px; fill: var(--brand-blue); }
  .brand-mark {
    position: absolute; right: 44px; top: 92px;
    display: flex; align-items: center; gap: 12px;
  }
  .brand-square { width: 22px; height: 22px; background: var(--brand-blue); }
  .brand-name {
    color: var(--brand-blue);
    font-size: 34px; font-weight: 600; letter-spacing: 3px; text-transform: uppercase;
  }
  .address {
    position: absolute; right: 44px; top: 200px; text-align: right;
    color: var(--ink-gray); font-size: 16px; line-height: 26px;
  }
  .front-web {
    position: absolute; right: 44px; bottom: 46px;
    color: var(--ink-gray); font-size: 18px; letter-spacing: 0.5px;
  }
  .front-web strong { color: var(--brand-blue); font-weight: 500; }
  .front-tab {
    position: absolute; right: 44px; bottom: 0;
    width: 290px; height: 24px; background: var(--brand-blue);
  }

  /* Back */
  .card-back {
    background: radial-gradient(circle at 30% 30%, var(--brand-blue) 0%, var(--brand-blue-deep) 100%);
    display: flex; flex-direction: column; align-items: center; justify-content: center;
  }
  .back-brand {
    color: var(--paper);
    font-size: 64px; font-weight: 600; letter-spacing: 8px; text-transform: uppercase;
    display: flex; align-items: center; gap: 20px;
  }
  .back-square { width: 36px; height: 36px; background: var(--paper); }
  .back-web {
    margin-top: 40px;
    display: flex; align-items: center; gap: 18px;
    color: var(--paper); font-size: 18px; letter-spacing: 1px;
  }
  .back-web .rule { width: 130px; height: 1px; background: rgba(251,251,251,0.6); }
</style>
</head>
<body>
  <section class="card card-front">
    <div class="holder">
      <h1 class="holder-name">Daniel Harper</h1>
      <p class="holder-role">Director</p>
    </div>
    <div class="brand-mark">
      <span class="brand-square"></span>
      <span class="brand-name">Norvale Group</span>
    </div>
    <div class="divider"></div>
    <ul class="contact">
      <li>
        <svg viewBox="0 0 24 24" aria-hidden="true"><path d="M6.6 10.8a15.1 15.1 0 0 0 6.6 6.6l2.2-2.2a1 1 0 0 1 1-.25 11.4 11.4 0 0 0 3.6.57 1 1 0 0 1 1 1V20a1 1 0 0 1-1 1A17 17 0 0 1 3 4a1 1 0 0 1 1-1h3.5a1 1 0 0 1 1 1c0 1.25.2 2.45.57 3.57a1 1 0 0 1-.25 1z"/></svg>
        (555) 014-2290
      </li>
      <li>
        <svg viewBox="0 0 24 24" aria-hidden="true"><path d="M3 5h18v14H3z M4.5 6.5v.4l7.5 5.2 7.5-5.2v-.4z" fill-rule="evenodd"/></svg>
        hello@norvalegroup.com
      </li>
    </ul>
    <address class="address" style="font-style:normal">
      42 Harbour Lane,<br>Ashford, NZ, 8020
    </address>
    <p class="front-web">www.<strong>norvalegroup</strong>.com</p>
    <div class="front-tab"></div>
  </section>

  <section class="card card-back">
    <div class="back-brand">
      <span class="back-square"></span>
      <span>Norvale Group</span>
    </div>
    <div class="back-web">
      <span class="rule"></span>
      <span>www.norvalegroup.com</span>
      <span class="rule"></span>
    </div>
  </section>
</body>
</html>
```